WordPress Site That Reviews Footwear

We need a wordpress web design for an affiliate site called PaceKite. We review and do roundups on footwear products. The final design should be clean and mobile friendly. The site should be built with Gutenberg page builder. We like the design of https://lunavessel.com/.
Updates

Need extra days to review

Target Market(s)

USA

Industry/Entity Type

Footwear

Logo Text

PaceKite

Number of Pages Required

4 page

Font styles to use
Serif
Sans Serif

Requirements
Must have
• Wordpress site
Blog post
Page
Categories
Homepage

```html
<!DOCTYPE html>
<html lang="en">
<head>
<meta charset="utf-8">
<title>PaceKite — Footwear Reviews</title>
<link href="https://fonts.googleapis.com/css2?family=Poppins:wght@400;500;600;700&display=swap" rel="stylesheet">
<style>
:root{
  --ink:#111;
  --muted:#6b6b6b;
  --lilac:#eedcf7;
  --green:#0b3b33;
  --red:#c01f2a;
  --coral:#ee4d4d;
  --yellow:#fbb72f;
  --star:#f5b400;
  --white:#fff;
  --black:#000;
}
*{margin:0;padding:0;box-sizing:border-box}
html,body{width:1200px;height:2484px;overflow:hidden}
body{font-family:"Poppins",sans-serif;color:var(--ink);background:var(--white);position:relative}
.abs{position:absolute}
a{color:inherit;text-decoration:none}

/* header */
.site-header{left:0;top:0;width:1200px;height:80px;background:var(--white)}
.brand{left:111px;top:24px;font-size:21px;font-weight:600}
.main-nav{left:620px;top:27px;display:flex;gap:31px;font-size:14px}
.social{display:flex;gap:5px}
.social span{width:26px;height:26px;border-radius:50%;background:var(--black);display:block}
.header-social{left:1003px;top:23px}

/* hero */
.hero{left:0;top:80px;width:1200px;height:467px;background:linear-gradient(90deg,#efdcf8 0%,#ead6f4 60%,#dcc8e6 100%)}
.hero-title{left:109px;top:212px;font-size:60px;font-weight:700;line-height:1;letter-spacing:-.5px}
.hero-text{left:111px;top:285px;width:380px;font-size:13px;line-height:20px;color:#555}
.hero-btn{left:112px;top:373px;background:var(--coral);color:var(--white);font-size:11.5px;padding:7px 16px;border-radius:2px;letter-spacing:.2px}
.cat-grid{left:557px;top:186px;display:grid;grid-template-columns:repeat(3,170px);grid-auto-rows:123px;gap:10px 11px}
.cat-card{background:var(--white);border:1px solid #b9b2bc;display:flex;flex-direction:column;align-items:center;justify-content:flex-end;padding-bottom:12px;font-size:18px;font-weight:500}
.cat-card svg{margin-bottom:10px}

/* size section */
.section-head{left:0;width:1200px;text-align:center}
.size-head{top:598px}
.section-head h2{font-size:27px;font-weight:500}
.section-head p{font-size:15.5px;color:var(--muted);margin-top:8px}
.features{left:0;top:700px;width:600px;height:426px;background:var(--green)}
.feature{width:200px;color:var(--white)}
.feature h3{font-size:19px;font-weight:600}
.feature p{font-size:10.5px;line-height:17px;margin-top:8px}
.feature .more{font-size:12.5px;margin-top:9px;display:flex;align-items:center;gap:6px}
.frame-red-1{left:583px;top:714px;width:532px;height:346px;background:var(--red)}
.shoes-photo{left:557px;top:740px;width:531px;height:346px;background:linear-gradient(135deg,#6b5648 0%,#c9c0b6 35%,#e9e4de 60%,#8a4630 100%)}

/* video */
.video-band{left:0;top:1126px;width:1200px;height:440px;background:var(--yellow)}
.video-head{top:1208px}
.video-head p{color:var(--ink)}
.frame-red-2{left:376px;top:1300px;width:724px;height:471px;background:var(--red)}
.video-still{left:100px;top:1332px;width:972px;height:469px;background:linear-gradient(90deg,#8a6b57 0%,#d8d5cf 30%,#8fa6c4 55%,#d9d6d0 80%,#7b6354 100%)}
.play{left:558px;top:1537px;width:58px;height:58px;border-radius:50%;background:var(--red);display:flex;align-items:center;justify-content:center}
.nav-arrow{width:41px;height:41px;background:var(--black);display:flex;align-items:center;justify-content:center}
.vid-prev{left:43px;top:1547px}
.vid-next{left:1116px;top:1547px}

/* testimonials */
.testi-head{left:112px;top:1858px}
.testi-head h2{font-size:27px;font-weight:500;line-height:39px}
.testi-head p{font-size:14px;line-height:22px;color:var(--muted);margin-top:12px;width:260px}
.testi-prev{left:112px;top:2024px}
.testi-next{left:170px;top:2024px}
.review{top:1867px;width:322px;height:210px;background:var(--white);box-shadow:0 2px 10px rgba(0,0,0,.18);padding:16px 14px}
.review .who{display:flex;align-items:center;gap:16px}
.avatar{width:66px;height:66px;border-radius:50%;background:linear-gradient(#8a7a70,#c9b8ab)}
.review h4{font-size:17px;font-weight:600}
.stars{color:var(--star);font-size:19px;letter-spacing:1px;line-height:1.4}
.review p{font-size:13.5px;line-height:19px;color:var(--muted);margin-top:12px;padding:0 2px}

/* footer */
.site-footer{left:0;top:2143px;width:1200px;height:341px;background:var(--black);color:var(--white)}
.foot-brand{left:109px;top:2168px;font-size:32px;font-weight:700}
.foot-about{left:109px;top:2229px;width:310px;font-size:13.5px;line-height:19px}
.foot-col h5{font-size:16px;font-weight:500;padding-bottom:10px;border-bottom:1px solid #aaa;width:111px}
.foot-col ul{list-style:none;margin-top:13px}
.foot-col li{font-size:13.5px;margin-bottom:17px}
.contact-list{list-style:none;margin-top:14px}
.contact-list li{display:flex;gap:18px;font-size:16px;font-weight:600;line-height:29px;margin-bottom:8px}
.contact-list svg{flex:none;margin-top:5px}
.foot-rule{left:109px;top:2416px;width:978px;height:1px;background:#555}
.legal{left:111px;top:2446px;font-size:13px}
.footer-social{left:966px;top:2443px}
.footer-social span{background:var(--white)}
</style>
</head>
<body>

<header class="site-header abs">
  <div class="brand abs">PaceKite</div>
  <nav class="main-nav abs"><a>Home</a><a>Products</a><a>Reviews</a><a>About</a><a>Contact</a></nav>
  <div class="social header-social abs"><span></span><span></span><span></span></div>
</header>

<section class="hero abs" role="img" aria-label="Soft lilac illustration of people sharing reviews beside leather shoes"></section>
<h1 class="hero-title abs">PaceKite</h1>
<p class="hero-text abs">Sed ut perspiciatis unde omnis iste natus error sit voluptatem accusantium doloremque laudantium, totam rem aperiam, eaque ipsa quae ab illo inventore veritatis et quasi architecto beatae vitae dicta sunt explicabo.</p>
<a class="hero-btn abs">CHECK OUT A FEW OF OUR FAVORITES REVIEWS</a>

<div class="cat-grid abs">
  <div class="cat-card"><svg width="56" height="48" viewBox="0 0 56 48" fill="none" stroke="#222" stroke-width="2"><rect x="3" y="3" width="44" height="34" rx="2"/><path d="M3 11h44M10 19h28M10 25h20"/><path d="M36 30l14 12-4 3-12-12z"/></svg>Finibus Bonorum</div>
  <div class="cat-card"><svg width="66" height="56" viewBox="0 0 66 56" fill="none" stroke="#222" stroke-width="2"><path d="M10 4l3 7 7 1-5 5 1 7-6-4-6 4 1-7-5-5 7-1z"/><rect x="16" y="14" width="46" height="30"/><path d="M26 24h28M26 32h28M48 44v8l-8-8"/></svg>Bonorum</div>
  <div class="cat-card"><svg width="60" height="60" viewBox="0 0 60 60" fill="none" stroke="#222" stroke-width="2"><path d="M6 30h10v26H6zM16 32l10-16 2-10c4 0 6 4 5 10l-2 8h14c3 0 4 4 2 6 2 2 1 5-1 6 1 2 0 5-2 6 1 3-1 6-4 6H16"/><path d="M46 4l2 5 5 1-4 3 1 5-4-3-4 3 1-5-4-3 5-1z"/></svg>Finibus</div>
  <div class="cat-card"><svg width="80" height="70" viewBox="0 0 80 70" fill="none" stroke="#222" stroke-width="2"><path d="M4 22h72l-6 10 6 10H4l6-10z"/><path d="M26 6l3 6 6 1-4 4 1 6-6-3-6 3 1-6-4-4 6-1zM46 6l3 6 6 1-4 4 1 6-6-3-6 3 1-6-4-4 6-1z"/><path d="M34 50h6l2-6c3 0 4 3 3 6h6c2 0 3 3 1 4 2 2 0 4-1 5 1 2-1 4-3 4H34z"/></svg>Finibus Bonorum</div>
  <div class="cat-card"><svg width="86" height="52" viewBox="0 0 86 52" fill="none" stroke="#222" stroke-width="2.5"><path d="M4 18c10 0 16-4 20-10 8 8 18 14 32 16 14 2 26 8 26 16v4H4z"/><path d="M4 48h78M30 14l6-6M36 18l6-6M42 22l6-6"/></svg>Finibus Bonorum</div>
  <div class="cat-card"><svg width="86" height="52" viewBox="0 0 86 52" fill="none" stroke="#222" stroke-width="2"><path d="M6 20c6 0 12-4 16-12 8 10 20 14 36 16 14 2 22 8 22 14v6H6z"/><path d="M6 44h74M28 28l14 14M40 26l12 14"/></svg>Finibus Bonorum</div>
</div>

<div class="section-head size-head abs">
  <h2>What’s your footwear Size?</h2>
  <p>Neque porro quisquam est qui dolorem ipsum quia dolor sit amet, consectetur, adipisci velit...</p>
</div>

<section class="features abs">
  <div class="feature abs" style="left:111px;top:90px"><h3>Perspiciatis</h3><p>Neque porro quisquam est qui dolorem ipsum quia dolor sit amet, consectetur, adipisci velit.</p><div class="more">Learn More <svg width="12" height="10" viewBox="0 0 12 10" fill="none" stroke="#fff" stroke-width="2"><path d="M1 5h9M6 1l4 4-4 4"/></svg></div></div>
  <div class="feature abs" style="left:333px;top:90px"><h3>Lorem Ipsum</h3><p>Neque porro quisquam est qui dolorem ipsum quia dolor sit amet, consectetur, adipisci velit.</p><div class="more">Learn More <svg width="12" height="10" viewBox="0 0 12 10" fill="none" stroke="#fff" stroke-width="2"><path d="M1 5h9M6 1l4 4-4 4"/></svg></div></div>
  <div class="feature abs" style="left:111px;top:228px"><h3>Consequuntur</h3><p>Neque porro quisquam est qui dolorem ipsum quia dolor sit amet, consectetur, adipisci velit.</p><div class="more">Learn More <svg width="12" height="10" viewBox="0 0 12 10" fill="none" stroke="#fff" stroke-width="2"><path d="M1 5h9M6 1l4 4-4 4"/></svg></div></div>
  <div class="feature abs" style="left:333px;top:228px"><h3>Finibus Bonorum</h3><p>Neque porro quisquam est qui dolorem ipsum quia dolor sit amet, consectetur, adipisci velit.</p><div class="more">Learn More <svg width="12" height="10" viewBox="0 0 12 10" fill="none" stroke="#fff" stroke-width="2"><path d="M1 5h9M6 1l4 4-4 4"/></svg></div></div>
</section>
<div class="frame-red-1 abs"></div>
<div class="shoes-photo abs" role="img" aria-label="Photo of several pairs of leather dress shoes and sneakers on a floor"></div>

<section class="video-band abs"></section>
<div class="section-head video-head abs">
  <h2>Watch our Review Video’s</h2>
  <p>Neque porro quisquam est qui dolorem ipsum quia dolor sit amet, consectetur, adipisci velit...</p>
</div>
<div class="frame-red-2 abs"></div>
<div class="video-still abs" role="img" aria-label="Video still of a reviewer speaking in front of a bookshelf"></div>
<div class="play abs"><svg width="20" height="22" viewBox="0 0 20 22"><path d="M2 1l17 10L2 21z" fill="#fff"/></svg></div>
<div class="nav-arrow vid-prev abs"><svg width="14" height="22" viewBox="0 0 14 22" fill="none" stroke="#fff" stroke-width="2.5"><path d="M12 2L3 11l9 9"/></svg></div>
<div class="nav-arrow vid-next abs"><svg width="14" height="22" viewBox="0 0 14 22" fill="none" stroke="#fff" stroke-width="2.5"><path d="M2 2l9 9-9 9"/></svg></div>

<div class="testi-head abs">
  <h2>Our Latest<br>Client Testmonials</h2>
  <p>Neque porro quisquam est qui dolorem ipsum quia dolor sit amet consectetur, adipisci velit...</p>
</div>
<div class="nav-arrow testi-prev abs"><svg width="14" height="22" viewBox="0 0 14 22" fill="none" stroke="#fff" stroke-width="2.5"><path d="M12 2L3 11l9 9"/></svg></div>
<div class="nav-arrow testi-next abs"><svg width="14" height="22" viewBox="0 0 14 22" fill="none" stroke="#fff" stroke-width="2.5"><path d="M2 2l9 9-9 9"/></svg></div>

<article class="review abs" style="left:422px">
  <div class="who"><div class="avatar" role="img" aria-label="Reviewer portrait"></div><div><h4>Marla T Quinlan</h4><div class="stars">★★★★★</div></div></div>
  <p>Lorem Ipsum is simply dummy text of the printing and typesetting industry. Lorem Ipsum has been the industry's standard dummy text ever since the 1500s, when an unknown printer took...</p>
</article>
<article class="review abs" style="left:765px">
  <div class="who"><div class="avatar" role="img" aria-label="Reviewer portrait"></div><div><h4>Marla T Quinlan</h4><div class="stars">★★★★★</div></div></div>
  <p>Lorem Ipsum is simply dummy text of the printing and typesetting industry. Lorem Ipsum has been the industry's standard dummy text ever since the 1500s, when an unknown printer took...</p>
</article>

<footer class="site-footer abs"></footer>
<div class="foot-brand abs" style="color:#fff">PaceKite</div>
<p class="foot-about abs" style="color:#fff">Sed ut perspiciatis unde omnis iste natus error sit voluptatem accusantium doloremque laudantium, totam rem aperiam, eaque ipsa quae ab illo inventore veritatis et quasi architecto beatae vitae dicta sunt explicabo. Nemo enim ipsam voluptatem quia voluptas sit aspernatur aut odit aut fugit,</p>
<div class="foot-col abs" style="left:465px;top:2179px;color:#fff"><h5>Useful</h5><ul><li>About PaceKite</li><li>Video Testimonials</li><li>How To Use</li><li>Contact Us</li></ul></div>
<div class="foot-col abs" style="left:643px;top:2179px;color:#fff"><h5>Company</h5><ul><li>PaceKite About</li><li>Lorem ipsum</li><li>Dolor sit amet</li><li>Lorem ipsum</li></ul></div>
<div class="foot-col abs" style="left:818px;top:2179px;color:#fff;width:280px"><h5>Contact</h5>
  <ul class="contact-list">
    <li><svg width="20" height="20" viewBox="0 0 24 24" fill="#fff"><path d="M6.6 10.8a15 15 0 006.6 6.6l2.2-2.2a1 1 0 011-.25 11.4 11.4 0 003.6.57 1 1 0 011 1V20a1 1 0 01-1 1A17 17 0 013 4a1 1 0 011-1h3.5a1 1 0 011 1c0 1.25.2 2.45.57 3.57a1 1 0 01-.25 1z"/></svg>+555-014-2290</li>
    <li><svg width="20" height="16" viewBox="0 0 20 16" fill="#fff"><path d="M0 2a2 2 0 012-2h16a2 2 0 012 2v.5l-10 6-10-6z"/><path d="M0 4.8l10 6 10-6V14a2 2 0 01-2 2H2a2 2 0 01-2-2z"/></svg>hello@pacekite-mail.com</li>
    <li><svg width="20" height="26" viewBox="0 0 20 26" fill="#fff"><path d="M10 0a10 10 0 0110 10c0 7-10 16-10 16S0 17 0 10A10 10 0 0110 0zm0 6a4 4 0 100 8 4 4 0 000-8z"/></svg>412 Alder Row, Brookfield,<br>Ohio 44000</li>
  </ul>
</div>
<div class="foot-rule abs"></div>
<p class="legal abs" style="color:#fff">PaceKite © 2021. ALL RIGHTS RESERVED | PRIVACY POLICY | TERMS AND CONDITIONS</p>
<div class="social footer-social abs"><span></span><span></span><span></span><span></span></div>

</body>
</html>
```